Flyer Design Project For Kitchen Rendering Service

We need an A4 Page flyer designed for a new kitchen rendering service we are launching. Our target market is other kitchen designers/manufacturers. We want them to outsource the rendering of their kitchen designs to us. Many kitchen designers still hand draw kitchens using pen and paper. This makes it hard for the end client to visualise how their new kitchen will look. Utilising specialist rendering software we transform hand drawn sketches into photographic quality renders. We provide a few different prospective renders per order giving the customer and their client a complete visualisation of the room.
Here is a few links to examples we would like to showcase.
This is the sketch our client provided: https://www.filmora-vault.net/s/qw8rtbnzx41kplm/Kitchen%20Sketch.pdf
Below is some links to the end result that we provided our client:
https://www.filmora-vault.net/s/h207xqpbnd53wr8/Kitchen%20Brochure%20Sample%2001.jpg
https://www.filmora-vault.net/s/ktaw9pmfrbx2zcy/Kitchen%20Brochure%20Sample%2003.jpg
https://www.filmora-vault.net/s/wep48nbv692hdsa/Kitchen%20Brochure%20Sample%2002.jpg
https://www.filmora-vault.net/s/gmx3rtuzp07yfkc/Kitchen%20Brochure%20Sample%2004.jpg
https://www.filmora-vault.net/s/b6nqwypa2h85jte/Kitchen%20Brochure%20Sample%2005.jpg
Our website for more info is www.hazelgrid.com.au
We only require two things from our client.
1. A drawing of any kind explaining the design (can be sketch, cad, photo, etc).
2. A completed 'Render Information From' That can be downloaded from the photographic render page of our website. http://www.hazelgrid.com.au/#!photographic-rendering/vmtb
The final design should communicate how easy it is for a kitchen designer/manufacturer to transform their basic drawings/sketchs to a photograph quality renders and help them win more jobs and boost sales using our service.
Reason: We have extended the deadline by a few days to allow us to review and provide feedback to some last minute designs that have been submitted. Thank you to all the designers that have submitted designs. Stay tuned for our feedback
Target Market(s)
Our target market is other kitchen designers/manufacturers
Industry/Entity Type
Software
Look and feel
Each slider illustrates characteristics of the customer's brand and the style your logo design should communicate.

```html
<!DOCTYPE html>
<html lang="en">
<head>
<meta charset="utf-8">
<title>Hazelgrid Kitchen Rendering Flyer</title>
<link href="https://fonts.googleapis.com/css2?family=Open+Sans:wght@400;600;700&display=swap" rel="stylesheet">
<style>
  :root {
    --blue: #2f8fd3;
    --blue-dark: #1f6fae;
    --sky: #d9ecf8;
    --sky-soft: #edf6fc;
    --ink: #333a40;
    --grey: #5f666c;
    --footer: #4a4f54;
    --white: #ffffff;
  }
  html, body { margin: 0; padding: 0; overflow: hidden; }
  body { width: 849px; height: 1200px; font-family: "Open Sans", Arial, sans-serif; }
  .flyer {
    position: relative; width: 849px; height: 1200px; overflow: hidden;
    background: linear-gradient(180deg, #ffffff 0%, #f3f6f8 60%, #e6ebee 100%);
  }
  .backdrop { position: absolute; inset: 0; }
  .brand {
    position: absolute; top: 34px; right: 40px;
    display: flex; align-items: center; gap: 10px;
  }
  .brand-dot { width: 44px; height: 44px; border-radius: 50%; background: var(--blue); }
  .brand-name { font-size: 30px; font-weight: 700; color: var(--blue); }
  .headline {
    position: absolute; top: 70px; left: 52px; margin: 0;
    font-weight: 400; font-size: 74px; line-height: 88px; color: var(--ink);
    letter-spacing: -1px;
  }
  .steps { position: absolute; top: 405px; left: 48px; width: 300px; }
  .step { display: flex; gap: 16px; margin-bottom: 42px; }
  .step-icon { width: 52px; height: 58px; flex: none; }
  .step-title { margin: 0; font-size: 38px; font-weight: 400; color: var(--blue); line-height: 44px; }
  .step-text { margin: 4px 0 0; font-size: 17px; line-height: 23px; color: var(--grey); }
  .render {
    position: absolute; border: 6px solid var(--white);
    box-shadow: 0 6px 16px rgba(0,0,0,.28);
  }
  .render-1 { top: 420px; left: 462px; width: 370px; height: 215px; transform: rotate(6deg);
    background: linear-gradient(160deg, #eef1f2 0%, #c9d0d4 55%, #6d767c 100%); }
  .render-2 { top: 630px; left: 548px; width: 300px; height: 185px; transform: rotate(8deg);
    background: linear-gradient(150deg, #f4f6f7 0%, #b9c2c7 60%, #5c666c 100%); }
  .render-3 { top: 790px; left: 500px; width: 330px; height: 170px; transform: rotate(7deg);
    background: linear-gradient(165deg, #e9eef0 0%, #aab4ba 55%, #4f585e 100%); }
  .render-4 { top: 930px; left: 420px; width: 420px; height: 160px; transform: rotate(-4deg);
    background: linear-gradient(175deg, #f7f8f9 0%, #d4dadd 55%, #9aa3a8 100%); }
  .difference { position: absolute; top: 915px; left: 54px; width: 335px; }
  .difference h2 { margin: 0 0 8px; font-size: 22px; font-weight: 700; color: var(--blue); }
  .difference p { margin: 0; font-size: 15px; line-height: 20px; color: var(--grey); }
  .price {
    position: absolute; top: 910px; left: 585px; width: 240px;
    padding: 6px 8px 10px;
    background: var(--blue); border: 4px solid var(--white); box-sizing: border-box;
    box-shadow: 0 4px 12px rgba(0,0,0,.25); color: var(--white); text-align: center;
  }
  .price-amount { margin: 0; font-size: 38px; font-weight: 700; line-height: 42px; }
  .price-unit { margin: 0; font-size: 23px; font-weight: 700; line-height: 27px; }
  .price-note { margin: 5px 0 0; font-size: 14px; line-height: 17px; }
  .footer {
    position: absolute; left: 0; bottom: 0; width: 849px; height: 92px;
    background: var(--footer); color: var(--white);
  }
  .footer-address { position: absolute; left: 52px; top: 14px; font-size: 16px; line-height: 21px; }
  .footer-address strong { font-weight: 700; }
  .social { position: absolute; left: 246px; top: 36px; display: flex; gap: 10px; }
  .social span { width: 28px; height: 28px; border-radius: 6px; background: #8a9096; }
  .call { position: absolute; right: 40px; top: 12px; text-align: right; }
  .call-phone { margin: 0; font-size: 30px; line-height: 36px; }
  .call-web { margin: 2px 0 0; font-size: 24px; font-weight: 700; line-height: 30px; }
</style>
</head>
<body>
<div class="flyer">
  <svg class="backdrop" width="849" height="1200" viewBox="0 0 849 1200" aria-hidden="true">
    <circle cx="150" cy="620" r="330" fill="var(--sky-soft)"/>
    <circle cx="90" cy="560" r="230" fill="var(--sky)" opacity=".7"/>
    <path d="M0 340 Q300 300 849 380 L849 420 Q300 350 0 390 Z" fill="#e3eef6" opacity=".6"/>
  </svg>

  <div class="brand">
    <span class="brand-dot"></span>
    <span class="brand-name">Hazelgrid</span>
  </div>

  <h1 class="headline">Quality Design<br>Makes Us Different</h1>

  <div class="steps">
    <div class="step">
      <svg class="step-icon" viewBox="0 0 52 58" aria-hidden="true">
        <path d="M6 4h30l10 10v40H6z" fill="none" stroke="var(--blue)" stroke-width="4"/>
        <path d="M16 42l18-18 5 5-18 18h-5z" fill="var(--blue)"/>
      </svg>
      <div>
        <h3 class="step-title">Step : 1</h3>
        <p class="step-text">Give us a drawing.<br>(Sketch, CAD, Photo)</p>
      </div>
    </div>
    <div class="step">
      <svg class="step-icon" viewBox="0 0 52 58" aria-hidden="true">
        <path d="M6 4h30l10 10v40H6z" fill="none" stroke="var(--blue)" stroke-width="4"/>
        <path d="M14 24h24M14 33h24M14 42h16" stroke="var(--blue)" stroke-width="4"/>
      </svg>
      <div>
        <h3 class="step-title">Step : 2</h3>
        <p class="step-text">Information: Complete our<br>'render information form'</p>
      </div>
    </div>
    <div class="step">
      <svg class="step-icon" viewBox="0 0 52 58" aria-hidden="true">
        <path d="M26 6l20 11v24L26 52 6 41V17z" fill="none" stroke="var(--blue)" stroke-width="4"/>
        <path d="M6 17l20 11 20-11M26 28v24" fill="none" stroke="var(--blue)" stroke-width="4"/>
      </svg>
      <div>
        <h3 class="step-title">Step : 3</h3>
        <p class="step-text">We create the 3D images<br>(up to 4 views per kitchen)</p>
      </div>
    </div>
  </div>

  <div class="render render-1" role="img" aria-label="Photographic render of a white modern kitchen with island bench"></div>
  <div class="render render-2" role="img" aria-label="Render of the kitchen from a second angle"></div>
  <div class="render render-3" role="img" aria-label="Render of kitchen island and dark splashback"></div>
  <div class="render render-4" role="img" aria-label="Close render of glossy white kitchen benchtop"></div>

  <div class="difference">
    <h2>The Hazelgrid Difference</h2>
    <p>We rendered Hazelgrid understands that your kitchen is the heart of your home. This is where families bond as they prepare an I need matter. We rendered Hazelgrid understands that your kitchen is the heart of your home. This is where families bond as they prepare an I need matter</p>
  </div>

  <div class="price">
    <p class="price-amount">$150-$200</p>
    <p class="price-unit">Per Kitchen</p>
    <p class="price-note">Price varies depending<br>on complexity of kitchen</p>
  </div>

  <footer class="footer">
    <div class="footer-address">
      <strong>Hazelgrid Pty Ltd</strong><br>
      Marlow Bay, NSW 2290<br>
      info@hazelgrid.com.au
    </div>
    <div class="social" aria-hidden="true"><span></span><span></span><span></span></div>
    <div class="call">
      <p class="call-phone">Call Now: 0491 570 226</p>
      <p class="call-web">www.hazelgrid.com.au</p>
    </div>
  </footer>
</div>
</body>
</html>
```